Awesome photographers card for an awesome new business

Double sided business card Black background and silver logo in middle on one side. Details on otherside. please keep it simple

Industry/Entity Type

Photographer

Contact Information for Business Card

Gerald Fenwick
0452817360
GeraldFenwickPhotography47@mailbox.test
www.GeraldFenwickPhotography.test.au
Instagram _Gerald_fenwick

Requirements
Must have
• My logo in Silver
• please use instagram logo instead of "Instagram"

```html
<!DOCTYPE html>
<html lang="en">
<head>
<meta charset="utf-8">
<title>Gerald Fenwick Photography – Business Card</title>
<link rel="stylesheet" href="https://fonts.googleapis.com/css2?family=Open+Sans:wght@400;600&family=Roboto+Condensed:wght@700&display=swap">
<style>
  :root {
    --backdrop: #3a332f;
    --card: #141414;
    --card-edge: #1d1d1d;
    --silver: #c9c9c9;
    --silver-dim: #8a8a8a;
    --text: #e6e6e6;
    --rule: #4a4a4a;
  }
  * { box-sizing: border-box; margin: 0; padding: 0; }
  html, body { width: 1200px; height: 864px; overflow: hidden; }
  body {
    background: var(--backdrop);
    font-family: "Open Sans", Arial, sans-serif;
    display: flex;
    align-items: center;
    justify-content: center;
    gap: 40px;
  }
  .card {
    position: relative;
    width: 540px;
    height: 309px;
    background: var(--card);
    border: 1px solid var(--card-edge);
    box-shadow: 0 14px 30px rgba(0,0,0,0.45);
    overflow: hidden;
  }

  /* Brand mark stand-in */
  .brand {
    display: flex;
    align-items: center;
    gap: 10px;
    color: var(--silver);
    font-family: "Open Sans", Arial, sans-serif;
    font-weight: 600;
    letter-spacing: 0.18em;
    text-transform: uppercase;
    line-height: 1.35;
  }
  .brand-dot {
    flex: none;
    border: 2px solid var(--silver);
    border-radius: 50%;
  }

  /* Front side */
  .card-front .brand {
    position: absolute;
    left: 50%;
    top: 82px;
    transform: translateX(-50%);
    font-size: 14px;
  }
  .card-front .brand-dot { width: 54px; height: 54px; }
  .card-front .website {
    position: absolute;
    left: 0; right: 0;
    top: 210px;
    text-align: center;
    color: var(--silver-dim);
    font-size: 14px;
    letter-spacing: 0.14em;
  }

  /* Back side */
  .holder-name {
    position: absolute;
    left: 40px;
    top: 108px;
    color: var(--text);
    font-family: "Roboto Condensed", "Arial Narrow", sans-serif;
    font-weight: 700;
    font-size: 19px;
    letter-spacing: 0.02em;
    text-transform: uppercase;
  }
  .name-rule {
    position: absolute;
    left: 40px;
    width: 290px;
    top: 140px;
    height: 1px;
    background: var(--rule);
  }
  .contact-list {
    position: absolute;
    left: 40px;
    top: 150px;
    list-style: none;
    color: var(--text);
    font-size: 13px;
    line-height: 19px;
  }
  .contact-list li { display: flex; align-items: center; gap: 10px; }
  .contact-icon { width: 11px; height: 11px; flex: none; fill: var(--silver-dim); }
  .card-back .brand {
    position: absolute;
    right: 26px;
    top: 122px;
    font-size: 9px;
    gap: 8px;
  }
  .card-back .brand-dot { width: 34px; height: 34px; }
  .base-rule {
    position: absolute;
    left: 250px;
    right: 30px;
    bottom: 40px;
    height: 1px;
    background: var(--rule);
  }
</style>
</head>
<body>
  <section class="card card-front" aria-label="Card front">
    <div class="brand">
      <span class="brand-dot"></span>
      <span>Gerald Fenwick<br>Photography</span>
    </div>
    <p class="website">www.GeraldFenwickPhotography.test.au</p>
  </section>

  <section class="card card-back" aria-label="Card back">
    <h1 class="holder-name">Gerald Fenwick</h1>
    <div class="name-rule"></div>
    <ul class="contact-list">
      <li>
        <svg class="contact-icon" viewBox="0 0 12 12" aria-hidden="true"><path d="M2.5 1h2l1 3-1.3 1a6 6 0 0 0 2.8 2.8l1-1.3 3 1v2a1 1 0 0 1-1 1A9.5 9.5 0 0 1 1.5 2a1 1 0 0 1 1-1z"/></svg>
        <span>0452817360</span>
      </li>
      <li>
        <svg class="contact-icon" viewBox="0 0 12 12" aria-hidden="true"><path d="M1 2.5h10v7H1z M1.5 3l4.5 3.5L10.5 3" stroke="#141414" stroke-width="0.8"/></svg>
        <span>GeraldFenwickPhotography47@mailbox.test</span>
      </li>
      <li>
        <svg class="contact-icon" viewBox="0 0 12 12" aria-hidden="true"><circle cx="6" cy="6" r="5"/><path d="M1 6h10M6 1c-2.5 3-2.5 7 0 10M6 1c2.5 3 2.5 7 0 10" stroke="#141414" stroke-width="0.8" fill="none"/></svg>
        <span>www.GeraldFenwickPhotography.test.au</span>
      </li>
      <li>
        <svg class="contact-icon" viewBox="0 0 12 12" aria-hidden="true"><circle cx="6" cy="6" r="5"/></svg>
        <span>_Gerald_fenwick</span>
      </li>
    </ul>
    <div class="brand">
      <span class="brand-dot"></span>
      <span>Gerald Fenwick<br>Photography</span>
    </div>
    <div class="base-rule"></div>
  </section>
</body>
</html>
```